Wesbite design for Investment Firm

We want a basic (clean) website that follows the form, fonts and colors of our attachments. This is for a financial investment management firm, but we have a boutique (anti-Wall Street) approach. Site should have an Home Page (Logo up top - room for basic copy on bottom, Philosophy Page (room for Quarterly Letter attachment and basic copy, Performance Page (room for Performance Overview and Performance Analysis and basic copy), Team Page, Commentary Page and Contact

Reason: Some designers have asked for an extension. Again, please only use image of Train Station or Train Station Logo in design.

Target Market(s)

Small and mid-size financial advisors from across the country

Industry/Entity Type

Financial

Number of Pages Required

5+ page

Font styles to use
Other font styles liked:
• Palotino Linotype

Colors
3176b5
cfdeed
ffffff

Requirements
Must have
• Please refer to existing site www.qlvor.example. Of note, this is too complex / cluttered. We simply want Blur, Grey and White consistent with attachments. The copy is pretty good, but will be simplified (and no quotes)
Should not have
• No images other than train station logo and / or train station image

```html
<!DOCTYPE html>
<html lang="en">
<head>
<meta charset="utf-8">
<title>Larkfield Investment Company</title>
<link href="https://fonts.googleapis.com/css2?family=EB+Garamond:wght@400;500&family=Lato:wght@300;400;700;900&display=swap" rel="stylesheet">
<style>
:root{
  --stage:#333333;
  --navy:#0b0b72;
  --navy-deep:#101077;
  --sky:#cfdeed;
  --blue:#3176b5;
  --orange:#f89c14;
  --gold:#9a7418;
  --ink:#5c5c66;
  --line:#dcdfe6;
  --white:#ffffff;
  --red:#a83a3e;
}
*{box-sizing:border-box;margin:0;padding:0}
html,body{width:1200px;height:1200px;overflow:hidden;background:var(--stage)}
body{font-family:"Lato",sans-serif;position:relative}
.page{position:absolute;left:270px;top:0;width:824px;height:1500px;background:var(--white);transform:scale(.8);transform-origin:0 0;overflow:hidden}
.abs{position:absolute}

/* header */
.masthead{left:0;top:0;width:824px;height:69px;background:var(--sky);border-top:2px solid var(--navy)}
.brand{left:0;top:4px;width:824px;text-align:center;font-family:"EB Garamond",serif;font-size:21px;color:var(--navy);font-weight:500}
.tagline{left:0;top:30px;width:824px;text-align:center;font-family:"EB Garamond",serif;font-size:10px;color:var(--gold)}
.nav{top:50px;font-size:9px;color:#444;line-height:16px}
.nav-home{left:195px;width:40px;height:18px;border:2px solid var(--navy);text-align:center;line-height:14px;color:var(--navy)}
.btn-login{left:538px;width:44px;height:17px;border:1.5px solid var(--orange);border-radius:5px;text-align:center;color:var(--orange);line-height:14px}
.btn-signup{left:584px;width:46px;height:17px;background:var(--orange);border-radius:5px;text-align:center;color:#fff;line-height:17px}

/* hero */
.hero{left:0;top:70px;width:824px;height:327px;background:linear-gradient(100deg,#2a5a9e 0%,#5f86b8 22%,#d9dde2 45%,#f1f1ee 65%,#c9ccd0 85%,#47607e 100%)}
.hero-title{left:130px;top:148px;font-size:36px;font-weight:900;color:#fff;letter-spacing:-.5px}
.hero-copy{left:130px;top:201px;width:220px;font-size:9.5px;font-weight:700;color:#fff;line-height:15.5px}
.hero-btn{left:129px;top:264px;width:103px;height:29px;background:var(--orange);border-radius:4px;color:#fff;font-size:9px;font-weight:700;text-align:center;line-height:29px}

/* philosophy */
.section-title{left:130px;top:428px;font-size:18px;font-weight:300;color:#333}
.section-rule{left:130px;top:454px;width:77px;height:3px;border-top:1px solid var(--blue);border-bottom:1px solid var(--blue)}
.divider{left:130px;top:707px;width:377px;height:1px;background:#eceef2}
.card{left:158px;width:318px;background:#fff;border:1px solid var(--line);border-radius:4px;box-shadow:0 1px 3px rgba(0,0,0,.08);overflow:hidden}
.card-head{height:31px;background:var(--navy);color:#fff;font-size:12px;line-height:31px;padding-left:17px}
.card-body{padding:8px 17px 0;font-size:9px;color:var(--ink);line-height:15.3px}

/* sidebar */
.side{width:138px;background:#fff;border:1px solid var(--line);border-radius:4px;box-shadow:0 1px 3px rgba(0,0,0,.08)}
.side-title{position:absolute;left:7px;font-size:8.5px;color:var(--navy)}
.thumb{position:absolute;border:1px solid #666;background:linear-gradient(#fafafa,#eeeeee)}
.btn{position:absolute;height:21px;border-radius:5px;color:#fff;font-size:8px;font-weight:700;text-align:center;line-height:21px}
.btn-navy{background:var(--navy)}
.btn-orange{background:var(--orange)}
.post-title{position:absolute;left:7px;top:25px;font-size:10px;color:var(--orange);line-height:10px}
.post-date{position:absolute;left:9px;top:51px;font-size:5.5px;font-weight:700;color:var(--navy)}
.post-copy{position:absolute;left:7px;top:66px;width:118px;font-size:7.5px;color:#333;line-height:15.3px}

/* footer */
.footer{left:0;top:1190px;width:824px;height:310px;background:linear-gradient(180deg,var(--navy-deep) 0%,#14147e 55%,#1c1c8a 100%)}
.foot-h{font-size:8.5px;font-weight:700;color:#fff;top:1211px}
.foot-list{top:1228px;font-size:7.5px;line-height:15.3px;color:#b9c1ee;list-style:none}
.foot-list .hot{color:var(--orange)}
.foot-list .under{text-decoration:underline;color:var(--orange)}
.map{left:415px;top:1230px;width:121px;height:134px;border-radius:4px;background:linear-gradient(135deg,#dfe3ea,#c8d0dc)}
.contact{left:434px;font-size:7.5px;color:#fff;line-height:11px}
.field{left:552px;width:125px;border-bottom:1px solid #6f74b5;font-size:7.5px;color:#9ea5d6;padding-bottom:3px}
.btn-sub{left:552px;top:1335px;width:63px;height:17px;background:var(--red);border-radius:4px;color:#fff;font-size:7.5px;text-align:center;line-height:17px}
.legal{left:0;width:824px;text-align:center;font-size:7.5px;color:#fff}
</style>
</head>
<body>
<div class="page">
  <header class="abs masthead"></header>
  <div class="abs brand">Larkfield Investment Company</div>
  <div class="abs tagline">Separately Managed Accounts</div>
  <nav>
    <div class="abs nav nav-home">Home</div>
    <div class="abs nav" style="left:249px">Philosophy</div>
    <div class="abs nav" style="left:313px">Performance</div>
    <div class="abs nav" style="left:385px">Team</div>
    <div class="abs nav" style="left:427px">Letters</div>
    <div class="abs nav" style="left:475px">Commentary</div>
    <div class="abs nav btn-login" style="top:49px">Login</div>
    <div class="abs nav btn-signup" style="top:49px">Signup</div>
  </nav>

  <div class="abs hero" role="img" aria-label="Photograph of a white clapboard train station under a blue sky"></div>
  <h1 class="abs hero-title">WELCOME!</h1>
  <p class="abs hero-copy">The high expectations of our original investors is a key contributor to our value driven investment philosophy.</p>
  <div class="abs hero-btn">JOIN US</div>

  <h2 class="abs section-title">Philosophy</h2>
  <div class="abs section-rule"></div>
  <div class="abs divider"></div>

  <article class="abs card" style="top:490px;height:157px">
    <div class="card-head">Buy at a Discount</div>
    <div class="card-body">Our proprietary investment research seeks to determine the appraised value of a company. Investments are then made at a significant discount, ideally 20% to 40% below the company's current intrinsic value<br>This approach allows us to buy companies with a sufficient margin of safety, as valuations are imprecise and the future is unpredictable.</div>
  </article>
  <article class="abs card" style="top:673px;height:157px">
    <div class="card-head">Emphasis on Risk</div>
    <div class="card-body">Defining risk as the permanent loss of capital, we believe that the quality of investment decisions is far more important that the quantity of investment decisions.<br>Our process demands that we not trade stocks, but rather consider businesses we would like and purchase and hold for 5 to 10 years. We therefore mitigate risk via a thorough examination and understanding of each business we fractionally own.</div>
  </article>
  <article class="abs card" style="top:856px;height:157px">
    <div class="card-head">Willingness to Hold Cash</div>
    <div class="card-body">Patience is necessary in the absence of obvious bargains, as entry price is a significant determinant of return.<br>As great ideas are often scarce, it can take a long time for the market to present truly compelling opportunities that coincide with our circle of competence. As a result, we are content to hold cash until our patience is rewarded.</div>
  </article>

  <aside class="abs side" style="left:532px;top:437px;height:253px">
    <div class="side-title" style="top:6px">Process Overview</div>
    <div class="thumb" style="left:8px;top:21px;width:122px;height:157px" role="img" aria-label="Cover page of the process overview document"></div>
    <div class="btn btn-navy" style="left:9px;top:190px;width:119px">Read</div>
    <div class="btn btn-orange" style="left:9px;top:218px;width:119px">Download PDF</div>
  </aside>
  <aside class="abs side" style="left:534px;top:712px;height:189px">
    <div class="side-title" style="top:7px">Performance Analysis</div>
    <div class="thumb" style="left:6px;top:21px;width:121px;height:93px" role="img" aria-label="Cover page of the performance analysis report with a bar chart"></div>
    <div class="btn btn-navy" style="left:8px;top:126px;width:119px">Read</div>
    <div class="btn btn-orange" style="left:8px;top:154px;width:119px">Download PDF</div>
  </aside>
  <aside class="abs side" style="left:534px;top:924px;height:209px">
    <div class="side-title" style="top:11px">Latest Commentary</div>
    <div class="post-title">Core Equity Portfolio<br>Q2 2017</div>
    <div class="post-date">AUGUST 10, 2017</div>
    <p class="post-copy">Based on our estimate of fair value relative to the company's current stock price, we determine each company's current margin of safety in the Core Equity...</p>
    <div class="btn btn-orange" style="left:10px;top:172px;width:118px">Read More</div>
  </aside>

  <footer class="abs footer" role="img" aria-label="Night city skyline tinted deep blue"></footer>
  <div class="abs foot-h" style="left:163px">Site Map</div>
  <ul class="abs foot-list" style="left:163px">
    <li>Home</li><li>Philosophy</li><li>Performance</li><li>Team</li><li>Letters</li><li>Commentary</li><li class="hot">Login</li><li class="hot">Signup</li>
  </ul>
  <div class="abs foot-h" style="left:266px">Quick Links</div>
  <ul class="abs foot-list" style="left:266px">
    <li class="under">Performance Overview</li><li>Performance Analysis</li><li>Verification Statement</li><li>Larkfield ADV Part 2</li>
  </ul>
  <div class="abs foot-h" style="left:416px">Contact Us</div>
  <div class="abs map" role="img" aria-label="Street map showing the office location"></div>
  <svg class="abs" style="left:423px;top:1368px" width="10" height="70" viewBox="0 0 10 70">
    <path d="M5 1a3.5 3.5 0 0 0-3.5 3.5C1.5 7.5 5 11 5 11s3.5-3.5 3.5-6.5A3.5 3.5 0 0 0 5 1z" fill="#5cc35a"/>
    <circle cx="5" cy="4.5" r="1.3" fill="#14147e"/>
    <path d="M2 41c0 3 3 6 6 6l1-1.5-1.8-1.4-1 .8c-1-.5-2-1.5-2.5-2.5l.8-1-1.4-1.8z" fill="#5cc35a"/>
    <rect x="1" y="54" width="8" height="6" fill="#5cc35a"/>
    <path d="M1 54l4 3.2 4-3.2" fill="none" stroke="#14147e" stroke-width=".8"/>
  </svg>
  <div class="abs contact" style="top:1371px">4210 Harbor Glen Avenue,<br>Suite 210<br>Fairview, TX 75000</div>
  <div class="abs contact" style="top:1408px">555.010.4821</div>
  <div class="abs contact" style="top:1420px">info@qlvor.example</div>
  <div class="abs foot-h" style="left:552px">Subscribe to our Newsletter</div>
  <div class="abs field" style="top:1228px">your name</div>
  <div class="abs field" style="top:1253px">your email</div>
  <div class="abs field" style="top:1305px">your message</div>
  <div class="abs btn-sub">Subscribe</div>
  <div class="abs legal" style="top:1461px">Terms &amp; Condition &nbsp;&nbsp;&nbsp; Privacy</div>
  <div class="abs legal" style="top:1482px">qlvor.example 2017. All rights reserved.</div>
</div>
</body>
</html>
```